MRT Property - Business Cards

Looking for a business card & general letterhead, signage etc design for our new logo.

Colours:
000a20
0056a2
00b5ef
0088ce
68cef2

Fonts:
Poppins
Karla

Please keep look and feel of new brand - example in the zip package I sent.

```html
<!DOCTYPE html>
<html lang="en">
<head>
<meta charset="utf-8">
<title>MRT Property – Business Cards</title>
<link href="https://fonts.googleapis.com/css2?family=Poppins:wght@400;500;700;800&display=swap" rel="stylesheet">
<style>
  :root {
    --navy-deep: #000a20;
    --navy-card: #0b1230;
    --blue-brand: #0056a2;
    --blue-mid: #0088ce;
    --blue-bright: #00b5ef;
    --blue-soft: #68cef2;
    --pattern-violet: #4f63c9;
    --paper: #ffffff;
    --grey-shape: #e4e4e7;
    --ink: #1c1c22;
    --stage: #17171c;
  }
  * { margin: 0; padding: 0; box-sizing: border-box; }
  html, body { width: 1200px; height: 900px; overflow: hidden; }
  body {
    background: var(--stage);
    font-family: "Poppins", sans-serif;
    display: flex;
    flex-direction: column;
    align-items: center;
    justify-content: center;
    gap: 48px;
  }
  .card {
    position: relative;
    width: 700px;
    height: 400px;
    border-radius: 26px;
    overflow: hidden;
    box-shadow: 0 14px 30px rgba(0,0,0,.45);
  }

  /* Front */
  .card-front { background: var(--paper); }
  .front-decoration {
    position: absolute;
    right: 0; top: 150px;
    width: 430px; height: 250px;
    background: radial-gradient(ellipse at 45% 40%, var(--grey-shape) 0%, #eeeef0 55%, var(--paper) 80%);
  }
  .wordmark {
    position: absolute;
    font-family: "Poppins", sans-serif;
    font-weight: 800;
    color: var(--blue-brand);
    letter-spacing: .02em;
    white-space: nowrap;
  }
  .card-front .wordmark { left: 150px; top: 60px; font-size: 42px; }
  .wordmark-dot {
    display: inline-block;
    width: 22px; height: 22px;
    border-radius: 50%;
    background: var(--blue-bright);
    margin-right: 12px;
    vertical-align: middle;
  }
  .contact-list {
    position: absolute;
    left: 40px; top: 190px;
    list-style: none;
    font-size: 15px;
    line-height: 1.55;
    color: var(--ink);
  }
  .contact-list li { display: flex; align-items: center; gap: 8px; }
  .contact-list svg { width: 13px; height: 13px; fill: var(--blue-brand); flex: none; }
  .contact-address { margin-top: 8px; padding-left: 0; }
  .holder {
    position: absolute;
    right: 60px; top: 250px;
    text-align: left;
  }
  .holder-name {
    font-weight: 800;
    font-size: 30px;
    color: var(--blue-brand);
    letter-spacing: .01em;
    line-height: 1.1;
  }
  .holder-role {
    font-size: 16px;
    color: var(--ink);
    margin-top: 2px;
  }

  /* Back */
  .card-back { background: var(--navy-card); }
  .back-pattern {
    position: absolute; inset: 0;
    background: linear-gradient(135deg, #0a1028 0%, #18245a 45%, #2b3b8e 70%, #121a40 100%);
  }
  .card-back .wordmark {
    right: 50px; bottom: 60px;
    font-size: 40px;
    color: var(--paper);
  }
</style>
</head>
<body>

  <section class="card card-front">
    <div class="front-decoration" role="img" aria-label="Large faint grey brand mark in the lower right of the card"></div>

    <div class="wordmark"><span class="wordmark-dot"></span>MRT Property</div>

    <ul class="contact-list">
      <li>
        <svg viewBox="0 0 24 24"><path d="M6.6 10.8a15.1 15.1 0 0 0 6.6 6.6l2.2-2.2c.3-.3.7-.4 1-.2 1.1.4 2.3.6 3.6.6.6 0 1 .4 1 1V20c0 .6-.4 1-1 1A17 17 0 0 1 3 4c0-.6.4-1 1-1h3.5c.6 0 1 .4 1 1 0 1.3.2 2.5.6 3.6.1.3 0 .7-.2 1z"/></svg>
        +1- 555-013-2947
      </li>
      <li>
        <svg viewBox="0 0 24 24"><path d="M2 5h20v14H2zm2 2v.5l8 5 8-5V7zm0 2.8V17h16V9.8l-8 5z"/></svg>
        info@mrtproperty.com
      </li>
      <li>
        <svg viewBox="0 0 24 24"><path d="M12 2a10 10 0 1 0 0 20 10 10 0 0 0 0-20zm6.9 9h-3a15 15 0 0 0-1.3-5.6A8 8 0 0 1 18.9 11zM12 4c.9 1.2 1.8 3.6 1.9 7h-3.8c.1-3.4 1-5.8 1.9-7zM9.4 5.4A15 15 0 0 0 8.1 11h-3a8 8 0 0 1 4.3-5.6zM5.1 13h3a15 15 0 0 0 1.3 5.6A8 8 0 0 1 5.1 13zM12 20c-.9-1.2-1.8-3.6-1.9-7h3.8c-.1 3.4-1 5.8-1.9 7zm2.6-1.4a15 15 0 0 0 1.3-5.6h3a8 8 0 0 1-4.3 5.6z"/></svg>
        www.mrtproperty.com
      </li>
      <li class="contact-address">4820 Harbor Ridge Road</li>
      <li>#12, Suite Lakeview</li>
    </ul>

    <div class="holder">
      <div class="holder-name">DANA WHITFIELD</div>
      <div class="holder-role">Founder &amp; Principal</div>
    </div>
  </section>

  <section class="card card-back">
    <div class="back-pattern" role="img" aria-label="Repeating brand mark pattern in navy and violet blue"></div>
    <div class="wordmark"><span class="wordmark-dot"></span>MRT Property</div>
  </section>

</body>
</html>
```